Web design

We need the design for the logo and website for a women fashion website. No coding required. The colors used should be neutral (maybe with a light touch of color), the style should be modern, slightly luxurious, not too crowded. The target market is young professionals who love trendy clothes.
Updates

Need extra days to review

Target Market(s)

Young professionals

Industry/Entity Type

Apparel

Number of Pages Required

5+ page

Font styles to use
Sans Serif
Other font styles liked:
• Montserrat, Engravers Gothic, Benton Sans, gotham-book

Colors

Designer to choose colors to be used in the design.

```html
<!DOCTYPE html>
<html lang="en">
<head>
<meta charset="utf-8">
<title>LUMA — Women's Fashion</title>
<link href="https://fonts.googleapis.com/css2?family=Lora:ital,wght@0,400;0,500;0,600;0,700;1,600&family=Roboto:wght@300;400&display=swap" rel="stylesheet">
<style>
:root{
  --cream:#f7ebdc;
  --cream-box:#f6e8d8;
  --sand:#dbc8ad;
  --ink:#3b3026;
  --ink-soft:#5a4f45;
  --muted:#9a9088;
  --rose:#e98a7a;
  --footer:#1f1d1c;
  --white:#ffffff;
}
*{box-sizing:border-box;margin:0;padding:0}
html,body{width:1200px;height:3493px;overflow:hidden}
body{position:relative;background:var(--white);font-family:'Lora',serif;color:var(--ink)}
.abs{position:absolute}

/* header + hero */
.hero{left:0;top:0;width:1200px;height:723px;background:linear-gradient(135deg,#f8eee2 0%,#f6e6d2 100%)}
.brand{left:75px;top:36px;font-family:'Lora',serif;font-size:27px;font-weight:400;color:var(--ink);letter-spacing:0.5px}
.brand-footer{left:75px;top:3240px;color:var(--white)}
.nav{top:47px;font-size:16px;color:var(--ink-soft)}
.nav .chev{display:inline-block;width:7px;height:7px;border-right:1.3px solid var(--ink-soft);border-bottom:1.3px solid var(--ink-soft);transform:rotate(45deg);margin:0 0 3px 5px}
.hero-title{left:69px;top:210px;font-size:68px;line-height:88px;font-weight:400;color:var(--ink)}
.hero-copy{left:70px;top:405px;width:520px;font-size:14.5px;line-height:29px;color:var(--ink)}
.btn-hero{left:68px;top:525px;width:167px;height:54px;background:var(--sand);font-size:20px;color:var(--ink);display:flex;align-items:center;justify-content:center;gap:8px}
.hero-photo{left:719px;top:156px;width:352px;height:567px;border-radius:170px 170px 0 0;background:linear-gradient(180deg,#6b4a3a 0%,#2a2220 35%,#1c1818 100%)}

/* features */
.feature{top:759px;width:332px;height:137px;background:var(--cream-box)}
.feature svg{position:absolute;left:30px;top:38px}
.feature h3{position:absolute;left:108px;top:26px;font-size:17px;font-weight:400;color:var(--ink)}
.feature p{position:absolute;left:108px;top:60px;width:205px;font-family:'Roboto',sans-serif;font-size:11.5px;line-height:23px;color:var(--muted)}

.section-title{left:0;width:1200px;text-align:center;font-size:46px;font-weight:400;color:var(--ink)}

/* products */
.product{top:1047px;width:248px}
.product .photo{width:248px;height:369px;background:linear-gradient(180deg,#d9d8dc 0%,#c9c8cc 100%)}
.swatches{display:flex;gap:8px;margin-top:11px}
.swatches i{width:13px;height:13px;display:block}
.product h4{font-size:16px;font-weight:400;margin-top:10px;color:var(--ink)}
.product .sub{font-family:'Roboto',sans-serif;font-size:11px;color:var(--muted);margin-top:4px}
.product .rate{font-family:'Roboto',sans-serif;font-size:11px;color:var(--ink-soft);margin-top:5px}
.product .rate span{color:var(--rose);letter-spacing:2px}
.product .price{font-family:'Roboto',sans-serif;font-size:11px;color:var(--rose);margin-top:6px}
.arrow{top:1220px;width:14px;height:14px;border-left:2px solid var(--ink);border-bottom:2px solid var(--ink)}
.pager{left:1051px;top:1551px;width:73px;height:29px;border:1px solid var(--ink);font-size:15px;display:flex;align-items:center;justify-content:center}

/* collection */
.collection{left:75px;top:1612px;width:1049px;height:517px;background:linear-gradient(120deg,#6c6a4c 0%,#a98a74 35%,#c9a99a 60%,#d4b6a6 100%)}
.collection-title{left:75px;top:1700px}
.btn-outline{left:526px;top:1926px;width:151px;height:48px;border:2px solid var(--white);color:var(--white);font-size:19px;font-weight:600;display:flex;align-items:center;justify-content:center}

.tag-sub{left:0;top:2238px;width:1200px;text-align:center;font-size:14px;color:var(--ink)}
.insta{top:2292px;width:249px;height:287px}

/* newsletter */
.newsletter{left:0;top:2651px;width:1200px;height:522px;background:linear-gradient(90deg,#4f5442 0%,#8a8174 45%,#b0a497 70%,#9c8a7c 100%)}
.nl-label{left:75px;top:2811px;font-family:'Roboto',sans-serif;font-size:12px;color:var(--white);letter-spacing:0.3px}
.nl-title{left:73px;top:2853px;font-size:29px;line-height:42px;color:var(--white);font-weight:400}
.nl-field{left:75px;top:2986px;width:386px;border-bottom:1.5px solid var(--white);padding-bottom:2px;display:flex;justify-content:space-between;font-size:15px;color:var(--white)}

/* footer */
.footer{left:0;top:3173px;width:1200px;height:320px;background:var(--footer)}
.foot-about{left:73px;top:3288px;width:290px;font-family:'Roboto',sans-serif;font-size:11.5px;line-height:31.5px;color:#d8d4cf}
.foot-col{top:3238px}
.foot-col h5{font-size:19px;font-weight:600;color:var(--white);margin-bottom:18px}
.foot-col li{list-style:none;font-family:'Roboto',sans-serif;font-size:11.5px;line-height:31.5px;color:#d8d4cf}
.social{display:flex;gap:14px;margin-top:8px}
.social i{width:8px;height:8px;border-radius:50%;background:#e6e2dd;display:block}
.copyright{left:0;top:3458px;width:1200px;text-align:center;font-family:'Roboto',sans-serif;font-size:11px;color:#3d3936}
</style>
</head>
<body>

<section class="abs hero"></section>
<div class="abs hero-photo" role="img" aria-label="Smiling model in a black floral wrap dress"></div>

<header>
  <div class="abs brand">LUMA</div>
  <nav>
    <span class="abs nav" style="left:217px">Latest Arrivals</span>
    <span class="abs nav" style="left:358px">Clothes<span class="chev"></span></span>
    <span class="abs nav" style="left:465px">Sale</span>
    <span class="abs nav" style="left:870px">
      <svg width="14" height="14" viewBox="0 0 14 14" style="vertical-align:-2px;margin-right:10px"><circle cx="6" cy="6" r="4.5" fill="none" stroke="#3b3026" stroke-width="1.5"/><line x1="9.3" y1="9.3" x2="13" y2="13" stroke="#3b3026" stroke-width="1.5"/></svg>Search</span>
    <span class="abs nav" style="left:976px">En<span class="chev"></span></span>
    <svg class="abs" style="left:1036px;top:44px" width="16" height="19" viewBox="0 0 16 19"><path d="M5 5V3.5a3 3 0 0 1 6 0V5" fill="none" stroke="#3b3026" stroke-width="1.5"/><rect x="1" y="5" width="14" height="13" rx="1" fill="#3b3026"/></svg>
    <span class="abs nav" style="left:1081px">Log In</span>
  </nav>
</header>

<h1 class="abs hero-title">Mid season Sale<br>Upto 60% off</h1>
<p class="abs hero-copy">Lorem ipsum dolor sit amet, consectetur adipisicing elit, sed do eiusmod tempor incididunt ut labore et dolore magna aliqua. Ut enim ad minim veniam, quis nostrud.</p>
<a class="abs btn-hero">Shop Now <svg width="18" height="10" viewBox="0 0 18 10"><path d="M0 5h16M12 1l4 4-4 4" fill="none" stroke="#3b3026" stroke-width="1.4"/></svg></a>

<div class="abs feature" style="left:75px">
  <svg width="56" height="56" viewBox="0 0 56 56" fill="none" stroke="#3b3026" stroke-width="2"><circle cx="28" cy="28" r="25"/><ellipse cx="28" cy="28" rx="11" ry="25"/><line x1="3" y1="28" x2="53" y2="28"/><path d="M7 15h42M7 41h42"/></svg>
  <h3>Worldwide Shipping</h3>
  <p>Lorem ipsum dolor sit amet, conseur adipisicing.</p>
</div>
<div class="abs feature" style="left:434px">
  <svg width="56" height="56" viewBox="0 0 56 56" fill="none" stroke="#3b3026" stroke-width="2"><path d="M4 18l8-12h30l8 12v26H4z"/><path d="M4 18h46M27 6v12"/><path d="M38 36l8 6 8-6M46 42V28"/></svg>
  <h3>30 Days Return Policy</h3>
  <p>Lorem ipsum dolor sit amet, conseur adipisicing.</p>
</div>
<div class="abs feature" style="left:792px">
  <svg width="66" height="62" viewBox="0 0 66 62" fill="none" stroke="#3b3026" stroke-width="2" style="top:30px"><rect x="2" y="26" width="26" height="32"/><rect x="7" y="42" width="10" height="8"/><circle cx="44" cy="22" r="16"/><text x="44" y="26" font-size="11" font-family="Roboto,sans-serif" font-weight="700" fill="#3b3026" stroke="none" text-anchor="middle">FREE</text></svg>
  <h3>Free Shipping</h3>
  <p>Lorem ipsum dolor sit amet, conseur adipisicing.</p>
</div>

<h2 class="abs section-title" style="top:938px">Shop Now</h2>

<div class="abs arrow" style="left:44px;transform:rotate(45deg)"></div>
<div class="abs arrow" style="left:1142px;transform:rotate(-135deg)"></div>

<article class="abs product" style="left:76px">
  <div class="photo" role="img" aria-label="Model in grey bandeau top and grey joggers"></div>
  <div class="swatches"><i style="background:#8d8d8d;outline:1px solid #555;outline-offset:-3px"></i><i style="background:#b9a07f"></i><i style="background:#5a6b34"></i><i style="background:#3b3031"></i><i style="background:#1b1b1b"></i><i style="background:#a05a48"></i></div>
  <h4>Selene</h4><p class="sub">Softloop Joggers - Grey Marle</p>
  <p class="rate"><span>★★★★★</span> ( 23 )</p><p class="price">$58</p>
</article>
<article class="abs product" style="left:344px">
  <div class="photo" role="img" aria-label="Model in rust ribbed bodycon dress"></div>
  <div class="swatches"><i style="background:#8d8d8d;outline:1px solid #555;outline-offset:-3px"></i><i style="background:#b9a07f"></i><i style="background:#5a6b34"></i><i style="background:#3b3031"></i><i style="background:#1b1b1b"></i><i style="background:#a05a48"></i></div>
  <h4>Iris</h4><p class="sub">Softloop Joggers - Grey Marle</p>
  <p class="rate"><span>★★★★★</span> ( 23 )</p><p class="price">$58</p>
</article>
<article class="abs product" style="left:609px">
  <div class="photo" role="img" aria-label="Model in cream knit midi dress"></div>
  <div class="swatches"><i style="background:#8d8d8d;outline:1px solid #555;outline-offset:-3px"></i><i style="background:#b9a07f"></i><i style="background:#5a6b34"></i><i style="background:#3b3031"></i><i style="background:#1b1b1b"></i><i style="background:#a05a48"></i></div>
  <h4>Odette</h4><p class="sub">Softloop Joggers - Grey Marle</p>
  <p class="rate"><span>★★★★★</span> ( 23 )</p><p class="price">$58</p>
</article>
<article class="abs product" style="left:876px">
  <div class="photo" role="img" aria-label="Model in rust button-front shirt dress"></div>
  <div class="swatches"><i style="background:#8d8d8d;outline:1px solid #555;outline-offset:-3px"></i><i style="background:#b9a07f"></i><i style="background:#5a6b34"></i><i style="background:#3b3031"></i><i style="background:#1b1b1b"></i><i style="background:#a05a48"></i></div>
  <h4>Selene</h4><p class="sub">Softloop Joggers - Grey Marle</p>
  <p class="rate"><span>★★★★★</span> ( 23 )</p><p class="price">$58</p>
</article>

<div class="abs pager">01 / 05</div>

<div class="abs collection" role="img" aria-label="Model in a blush pink belted dress beside tropical leaves"></div>
<svg class="abs collection-title" width="1049" height="220" viewBox="0 0 1049 220">
  <defs><path id="collection-arc" d="M190 180 Q 480 40 880 160"/></defs>
  <text font-family="Lora,serif" font-style="italic" font-weight="600" font-size="78" fill="#ffffff"><textPath href="#collection-arc" startOffset="50%" text-anchor="middle">Shop by Collection</textPath></text>
  <path d="M220 195 Q 480 90 850 200" fill="none" stroke="#ffffff" stroke-width="2"/>
</svg>
<a class="abs btn-outline">Shop Now</a>

<h2 class="abs section-title" style="top:2160px">#Veloura</h2>
<p class="abs tag-sub">Show off your updated lookto our instagram account, mention us : @Veloura &nbsp;#Veloura</p>

<div class="abs insta" style="left:75px;background:linear-gradient(180deg,#9aa08a,#e8b8bd)" role="img" aria-label="Woman in pink floral dress on a balustrade"></div>
<div class="abs insta" style="left:342px;background:linear-gradient(180deg,#ece7e1,#d9d2c8)" role="img" aria-label="Model in black one-shoulder top and flared trousers"></div>
<div class="abs insta" style="left:609px;background:linear-gradient(180deg,#8e8e8a,#4d6a8a)" role="img" aria-label="Couple in blue suit and blue satin dress"></div>
<div class="abs insta" style="left:876px;background:linear-gradient(180deg,#a3a78a,#e6e2d6)" role="img" aria-label="Woman in floral dress with headscarf and bouquet on grass"></div>

<section class="abs newsletter" role="img" aria-label="Woman in bucket hat and patterned blouse in a meadow"></section>
<p class="abs nl-label">LUMA NEWSLETTER</p>
<h2 class="abs nl-title">Get weekly style inspiration and<br>first dibs on the newest collections</h2>
<div class="abs nl-field"><span>Email Address</span><span>Sign Up →</span></div>

<footer class="abs footer"></footer>
<div class="abs brand brand-footer">LUMA</div>
<p class="abs foot-about">Lorem ipsum dolor sit amet, consectetur adipisicing elit, sed do eiusmod tempor incididunt ut labore et dolore magna aliqua. Ut enim ad minim veniam, quis nostrud exercitation ullamco laboris nisi ut aliquip ex</p>
<div class="abs foot-col" style="left:627px"><h5>Help</h5><ul><li>Email Address</li><li>Returns / Exchanges</li><li>FAQ</li><li>Delivery Info</li></ul></div>
<div class="abs foot-col" style="left:839px"><h5>Shop</h5><ul><li>Clothes</li><li>Sale</li><li>Latest Arrival</li><li>Account</li></ul></div>
<div class="abs foot-col" style="left:1006px"><h5>Legal</h5><ul><li>Terms &amp; Conditions</li><li>Privacy Policy</li><li>Follow Us</li></ul><div class="social"><i></i><i></i><i></i><i></i></div></div>
<p class="abs copyright">Copyright ©2021 Luma. All Rights Reserved</p>

</body>
</html>
```